Stationery Design Project for Marketing Consultancy

I have started a new consultancy business and require the following elements to be designed using existing logo:
• Business card
• Letterhead
• Envelope (DL, C4, C5)
• Microsoft word template for report writing
• A4 Presentation Folder
• Powerpoint template
COPY FOR FRONT AND BACK OF BUSINESS CARD
logo
'Measurable Marketing. Epic Results' slogan (but no need to use existing lockup with logo)
name, B Bus. Mktg, Grad Dip Digital Mktg, CPM (post nominal abbreviations in smaller font)
mobile: 04XX-XXX-XXX (I will give details to the winner to add)
website: www.tolvarin.com.au
email: info@tolvarin.com.au
COPY FOR LETTERHEAD
Logo
Company Name
Please, submit your designs that include business card, letterhead and envelope. Once selected the winner will be asked to complete the project by creating the rest of the artwork.
FINAL FILES
Print ready files to be supplied as well as Indesign files so that minor amends can be made if necessary in future.
• Layered vectors in EPS & PDF
• Screen quality JPEG & PNGs
ABOUT THE BUSINESS: TOLVARIN
I work with clients to understand their business challenges, developing and executing measurable marketing strategies tied to key business metrics. Services include:
Services include:
• Business planning and business development
• Marketing and brand strategy
• Insight-driven integrated campaigns
• Loyalty programs and retention marketing
• Marketing automation
• Direct marketing (traditional and digital)
• Content strategy and development
Hi everyone,
Target Market(s)
Corporate decision makers (heads of marketing, general managers etc) and small to medium sized business owners. Predominately male aged 35+
Industry/Entity Type
Marketing
Requirements
Must have
- BRAND PERSONALITY
The successful design will communicate brand personality. I am a professional, results-driven entrepreneur, but want to show off my creative flair.
MEMORABILITY
Looking for a unique and eye-catching design. Am considering special printing effects (die cuts, letterpress, interactive elements, embossing, foiling etc) or a striking minimalist approach.
Nice to have
- I have a mission that could be incorporated on reverse if room -
Turning insights into actions & passion into profit.
Should not have
- Use of pink or green.

```html
<!DOCTYPE html>
<html lang="en">
<head>
<meta charset="utf-8">
<title>Tolvarin – Business Card</title>
<link rel="stylesheet" href="https://fonts.googleapis.com/css2?family=Arimo:wght@400;700&display=swap">
<style>
  :root {
    --backdrop: #2b2a2b;
    --card-paper: #ecebe8;
    --card-dark: #3a3a3a;
    --ink: #3b3b3b;
    --ink-soft: #555555;
    --emboss-face: #333333;
    --emboss-light: #4a4a4a;
    --emboss-shade: #242424;
  }
  * { box-sizing: border-box; margin: 0; padding: 0; }
  html, body {
    width: 1200px; height: 901px; overflow: hidden;
    background: var(--backdrop);
    font-family: "Arimo", Arial, sans-serif;
  }
  .stage {
    position: relative; width: 1200px; height: 901px;
    display: flex; align-items: center; justify-content: center; gap: 48px;
  }
  .card {
    position: relative; width: 520px; height: 318px;
    border-radius: 2px;
  }
  /* Front – light stock */
  .card--front { background: var(--card-paper); color: var(--ink); }
  .holder { position: absolute; left: 38px; top: 112px; }
  .holder__name { font-size: 25px; font-weight: 400; letter-spacing: 0.2px; }
  .holder__credentials { margin-top: 6px; font-size: 14px; color: var(--ink-soft); }
  .contact {
    position: absolute; left: 38px; bottom: 44px;
    list-style: none; font-size: 15px; line-height: 1.35; color: var(--ink);
  }
  .brand-lockup {
    position: absolute; right: 34px; top: 36px;
    display: flex; align-items: center; gap: 10px;
  }
  .brand-lockup__mark {
    width: 30px; height: 30px; border-radius: 50%;
    background: var(--ink);
  }
  .brand-lockup__name {
    font-size: 26px; font-weight: 700; letter-spacing: 1px; color: var(--ink);
  }
  /* Back – dark stock, blind embossed */
  .card--back {
    background: var(--card-dark);
    display: flex; align-items: center; justify-content: center; gap: 18px;
  }
  .emboss-mark {
    width: 52px; height: 52px; border-radius: 50%;
    background: var(--emboss-face);
    box-shadow: inset 2px 2px 2px var(--emboss-shade), 1px 1px 0 var(--emboss-light);
  }
  .emboss-name {
    font-size: 48px; font-weight: 700; letter-spacing: 2px;
    color: var(--emboss-face);
    text-shadow: 1px 1px 0 var(--emboss-light), -1px -1px 0 var(--emboss-shade);
  }
</style>
</head>
<body>
<main class="stage">
  <section class="card card--front" aria-label="Business card front">
    <div class="brand-lockup">
      <span class="brand-lockup__mark"></span>
      <span class="brand-lockup__name">TOLVARIN</span>
    </div>
    <div class="holder">
      <p class="holder__name">Nadia Ferrell</p>
      <p class="holder__credentials">B Bus. Mktg, Grad Dip Digital Mktg, CPM</p>
    </div>
    <ul class="contact">
      <li>04XX-XXX-XXX</li>
      <li>info@tolvarin.com.au</li>
      <li>www.tolvarin.com.au</li>
    </ul>
  </section>

  <section class="card card--back" aria-label="Business card back">
    <span class="emboss-mark"></span>
    <span class="emboss-name">TOLVARIN</span>
  </section>
</main>
</body>
</html>
```